Furniture & Lighting Wholesaler Needs a Product Catalogue/Look Book

Our company, Vostre Merchant Co, imports quality hand-made furniture, lighting and decor from South Africa. Our products are well-designed and are designed to be used in up-market hotels and homes. Our primary customers are small- to medium-size retail shops.
We require a +/- 14-16 page look book (concept as per attached image) that will be used both in hard-copy and online. We have all of the necessary high-res images, descriptions/text etc. We need you to propose several design concepts from which we can choose, and then execute the design.
Please visit our website www.vostremerchant.example to see the products and their descriptions, as well as to get a feel for our style. Thank you for looking at our project!
Target Market(s)
Boutique Furniture Stores; Interior Designers
Industry/Entity Type
It Company
Font styles to use
Other font styles liked:
- Bauer Bodini and Open Sans Condensed
Look and feel
Each slider illustrates characteristics of the customer's brand and the style your logo design should communicate.

```html
<!DOCTYPE html>
<html lang="en">
<head>
<meta charset="utf-8">
<title>Vostre Merchant Co – Look Book Spread</title>
<link href="https://fonts.googleapis.com/css2?family=Marcellus&family=Montserrat:wght@400;600;700&family=Open+Sans:wght@400;600&display=swap" rel="stylesheet">
<style>
  :root {
    --bg: #dcdcdc;
    --paper: #ffffff;
    --gold: #a99a6b;
    --gold-dark: #8f8152;
    --ink: #333333;
    --charcoal-light: #4b4b4b;
    --charcoal-dark: #1e1e1e;
    --panel: #e4e4e4;
    --label: #2b2b2b;
    --footer-band: #e9e9e9;
  }
  * { box-sizing: border-box; margin: 0; padding: 0; }
  html, body { width: 1200px; height: 900px; overflow: hidden; background: var(--bg); }
  .spread {
    position: absolute; left: 40px; top: 250px; width: 1120px; height: 400px;
    display: flex; box-shadow: 0 8px 24px rgba(0,0,0,.18);
  }
  .page { position: relative; width: 560px; height: 400px; overflow: hidden; }

  /* Left page */
  .page--about { background: var(--paper); }
  .about-title {
    position: absolute; left: 95px; top: 28px;
    font-family: "Marcellus", serif; font-size: 30px; font-weight: 400; color: var(--gold); letter-spacing: 1px;
  }
  .side-tab {
    position: absolute; left: 0; top: 170px; width: 80px; height: 180px;
    background: var(--gold); border-top-right-radius: 18px;
  }
  .page-number {
    position: absolute; left: 0; top: 330px; width: 34px; height: 26px;
    background: var(--ink); color: #ddd; font: 9px "Open Sans", sans-serif;
    display: flex; align-items: center; justify-content: center; border-top-right-radius: 8px;
  }
  .feature-card {
    position: absolute; left: 62px; top: 80px; width: 340px; height: 250px;
    border-radius: 22px; overflow: hidden; background: var(--gold);
  }
  .feature-photo {
    height: 150px;
    background: linear-gradient(180deg, #6f7f92 0%, #b9c0c6 45%, #d8cdb5 62%, #b9a682 100%);
  }
  .feature-icons { display: flex; justify-content: space-around; padding: 14px 14px 0; }
  .feature { width: 70px; text-align: center; color: #f4efe2; font: italic 8px "Open Sans", sans-serif; line-height: 1.25; }
  .feature svg { display: block; margin: 0 auto 6px; }
  .about-copy {
    position: absolute; left: 414px; top: 78px; width: 134px;
    font: 6px/1.3 "Open Sans", sans-serif; color: var(--ink); text-align: justify;
  }
  .about-copy p { margin-bottom: 5px; }
  .about-copy .highlight { color: var(--gold); font-weight: 600; text-transform: uppercase; }
  .about-copy ul { list-style: none; }
  .about-copy li { position: relative; padding-left: 9px; margin-bottom: 4px; }
  .about-copy li::before {
    content: "✓"; position: absolute; left: 0; top: 0; font-size: 5.5px;
    border: 0.6px solid var(--ink); width: 6px; height: 6px; line-height: 6px; text-align: center;
  }
  .site-footer {
    position: absolute; right: 0; bottom: 12px; width: 180px; height: 20px;
    background: var(--footer-band); display: flex; align-items: center; gap: 8px; padding-left: 14px;
    font: 6.5px "Open Sans", sans-serif; color: #777;
  }
  .site-footer .mark { width: 10px; height: 10px; border: 2px solid var(--ink); }

  /* Right page */
  .page--contents { background: linear-gradient(135deg, var(--charcoal-light) 0%, var(--charcoal-dark) 70%); }
  .contents-panel {
    position: absolute; left: 190px; top: 140px; width: 290px; height: 200px;
    background: var(--panel); border: 4px solid var(--gold); border-radius: 22px;
  }
  .contents-label {
    position: absolute; left: 170px; top: 165px; width: 180px; height: 24px;
    background: var(--label); color: var(--gold);
    font: 400 12px "Marcellus", serif; letter-spacing: .5px; padding: 5px 0 0 10px;
  }
  .contents-list {
    position: absolute; left: 230px; top: 200px; list-style: none;
    font: 700 10px/14px "Montserrat", sans-serif; color: var(--ink);
  }
  .contents-list span { display: inline-block; width: 22px; }
</style>
</head>
<body>
<main class="spread">
  <section class="page page--about">
    <h1 class="about-title">ABOUT US</h1>
    <div class="side-tab"></div>
    <div class="page-number">2</div>

    <div class="feature-card">
      <div class="feature-photo" role="img" aria-label="Photo of an elephant herd crossing a dry savanna under a cloudy sky"></div>
      <div class="feature-icons">
        <div class="feature">
          <svg width="22" height="24" viewBox="0 0 22 24" fill="none" stroke="#f4efe2" stroke-width="1.4"><rect x="3" y="3" width="16" height="19" rx="1"/><rect x="7" y="1" width="8" height="4"/><line x1="6" y1="10" x2="16" y2="10"/><line x1="6" y1="14" x2="16" y2="14"/><line x1="6" y1="18" x2="13" y2="18"/></svg>
          Catalogue
        </div>
        <div class="feature">
          <svg width="26" height="24" viewBox="0 0 26 24" fill="none" stroke="#f4efe2" stroke-width="1.4"><path d="M2 18h6l6 3 9-5-2-2-7 3"/><path d="M8 18l4-4h6"/><path d="M15 12V5M15 8c-3 0-4-2-4-4 3 0 4 2 4 4zM15 7c0-3 2-4 5-4 0 3-2 4-5 4z"/></svg>
          Handmade Craftmanship
        </div>
        <div class="feature">
          <svg width="22" height="24" viewBox="0 0 22 24" fill="none" stroke="#f4efe2" stroke-width="1.4"><path d="M11 23s-8-8-8-13a8 8 0 0 1 16 0c0 5-8 13-8 13z"/><circle cx="11" cy="10" r="4"/></svg>
          Manufactured in South Africa
        </div>
        <div class="feature">
          <svg width="24" height="24" viewBox="0 0 24 24" fill="none" stroke="#f4efe2" stroke-width="1.4"><path d="M4 20C4 10 10 4 21 4c0 11-6 17-17 16z"/><path d="M4 20L15 9"/></svg>
          Sustainable
        </div>
      </div>
    </div>

    <div class="about-copy">
      <p>Our style is contemporary "safari chic" while studiously avoiding any overt tribal / African / village handicraft references. Vostre Merchant Co offers a wide variety of up-market products for the home such as decorative lighting, furniture, accessories, cushions and rugs. Products are handmade in South Africa of exotic indigenous materials such as feathers, ostrich eggs, leather, porcupine quills, suede, horns, ostrich skins, and a variety of game skins.</p>
      <p class="highlight">We operate a sustainable model of sourcing &amp; manufacturing. All of our products have been sourced from suppliers who are committed to ethical business practices. For clarity, this means that:</p>
      <ul>
        <li>All animal skulls have been sourced from game reserves where the animal has died in the wild, or been killed during a legislated cull</li>
        <li>All cow horns and leather have been sourced from farms whose primary business is raising cattle as a food source, and who sell the cow horns &amp; skins as a by-product of food production</li>
        <li>The artisans working in the tanneries and factories in which our products are made are paid a living wage, and who work in a environment that is regularly examined by independent regulators.</li>
      </ul>
    </div>

    <div class="site-footer"><span class="mark"></span>www.vostremerchant.example</div>
  </section>

  <section class="page page--contents">
    <div class="contents-panel"></div>
    <h2 class="contents-label">TABLE OF CONTENT</h2>
    <ol class="contents-list">
      <li><span>1.</span>Chandeliers</li>
      <li><span>2.</span>Lamps</li>
      <li><span>3.</span>Furniture</li>
      <li><span>4.</span>Wall Art</li>
      <li><span>5.</span>Hides &amp; Skins</li>
      <li><span>6.</span>Horns &amp; Skulls</li>
      <li><span>7.</span>Decor</li>
      <li><span>8.</span>Lamp Shades</li>
      <li><span>9.</span>Contact Us</li>
    </ol>
  </section>
</main>
</body>
</html>
```